high end kitchens , needing new logo and business card design .

im looking a very simple looking design but classy that will stand out , i would like the design to be in the colours black , silver , gold and grey , although all colours dont need to be used in design , back of card to have name on it derek fawcett , address and phone number and website address , maybe fb logo . adrress is 42 mill row , carrowmore , bt19 4qa , 07912488265 , front of the card im open to design , back of card very simple i will want it matt black with silver writing , writing doesnt need to be that big

Target Market(s)

people with kitchen projects .

Industry/Entity Type

Interior Design

Contact Information for Business Card

front of business card th on it with maybe tallow hearths under it wrote smaller , maybe the card to be mate black with the writing in a gloss black or silver

Logo Text

th . tallow hearths

Font styles to use
Sans Serif
Script

Colors
1b1b1b
919191
f6f6f6
848484
ffc214
ec1f27

Requirements
Must have
• clean and simple , not too fussy ,
Nice to have
• n/a
Should not have
• n/a

```html
<!DOCTYPE html>
<html lang="en">
<head>
<meta charset="utf-8">
<title>Tallow Hearths — Business Card</title>
<link href="https://fonts.googleapis.com/css2?family=Cinzel:wght@600;700&family=Questrial&display=swap" rel="stylesheet">
<style>
  :root {
    --backdrop: #1e1e1e;
    --card: #151515;
    --card-edge: #262626;
    --gold: #d4a94a;
    --gold-soft: #c9a054;
  }
  * { margin: 0; padding: 0; box-sizing: border-box; }
  html, body {
    width: 1200px; height: 900px; overflow: hidden;
    background: var(--backdrop);
  }
  .canvas {
    position: relative; width: 1200px; height: 900px;
    background: radial-gradient(ellipse at 60% 40%, #2a2a2a 0%, var(--backdrop) 70%);
  }
  .card {
    position: absolute; left: 260px; width: 680px; height: 390px;
    background: var(--card);
    border: 1px solid var(--card-edge);
    box-shadow: 0 12px 30px rgba(0,0,0,.55);
  }
  .card--front { top: 45px; }
  .card--back { top: 465px; }

  .front-mark {
    position: absolute; left: 0; right: 0; top: 150px;
    display: flex; align-items: center; justify-content: center; gap: 18px;
  }
  .mark-dot {
    width: 34px; height: 34px; border-radius: 50%;
    border: 2px solid var(--gold);
  }
  .wordmark {
    font-family: "Cinzel", serif; font-weight: 600;
    color: var(--gold); font-size: 30px; letter-spacing: 8px;
    text-transform: uppercase;
  }

  .back-company {
    position: absolute; left: 48px; top: 42px;
    font-family: "Cinzel", serif; font-weight: 600;
    color: var(--gold); font-size: 14px; letter-spacing: 7px;
    text-transform: uppercase;
  }
  .back-name {
    position: absolute; left: 62px; top: 96px;
    font-family: "Cinzel", serif; font-weight: 700;
    color: var(--gold); font-size: 24px; letter-spacing: 2px;
    text-transform: uppercase;
  }
  .back-details {
    position: absolute; left: 62px; top: 160px;
    font-family: "Questrial", sans-serif;
    color: var(--gold-soft); font-size: 19px; line-height: 1.3;
    list-style: none;
  }
  .back-details .gap { margin-top: 22px; }
  .back-ring {
    position: absolute; right: 40px; top: 40px;
    width: 310px; height: 310px;
  }
</style>
</head>
<body>
<main class="canvas">
  <section class="card card--front" aria-label="Card front">
    <div class="front-mark">
      <span class="mark-dot"></span>
      <span class="wordmark">Tallow Hearths</span>
    </div>
  </section>

  <section class="card card--back" aria-label="Card back">
    <p class="back-company">Tallow Hearths</p>
    <h1 class="back-name">Derek Fawcett</h1>
    <ul class="back-details">
      <li>42 mill row ,</li>
      <li>carrowmore , bt19 4qa</li>
      <li class="gap">07912488265</li>
      <li>info@tallowhearths.co.uk</li>
      <li>www.tallowhearths.co.uk</li>
    </ul>
    <svg class="back-ring" viewBox="0 0 310 310" aria-hidden="true">
      <circle cx="155" cy="155" r="150" fill="none" stroke="#d4a94a" stroke-width="3"/>
    </svg>
  </section>
</main>
</body>
</html>
```